kmvalerohub website

I need a new homepage design for my current website at www.KMValeroHub.com. I want someone to look at my current website and develop a more appealing homepage... right now the colors don't blend very well and it needs a facelift

Reason: This has been extended to September 10th

```html
<!DOCTYPE html>
<html lang="en">
<head>
<meta charset="utf-8">
<title>KM Valero Hub – Home</title>
<link href="https://fonts.googleapis.com/css2?family=Yanone+Kaffeesatz:wght@300;400;600&family=Lato:wght@400;700&display=swap" rel="stylesheet">
<style>
:root{
  --pink:#ee2d8f;
  --pink-deep:#e01f80;
  --pink-soft:#f25aa6;
  --green:#2f6b22;
  --dark:#2b2b2b;
  --white:#ffffff;
  --ink:#222222;
}
*{margin:0;padding:0;box-sizing:border-box}
html,body{width:722px;height:1200px;overflow:hidden;background:var(--white)}
body{position:relative;font-family:'Lato',sans-serif;color:var(--ink)}
.head{font-family:'Yanone Kaffeesatz',sans-serif}
.abs{position:absolute}

.hero-photo{left:0;top:0;width:722px;height:365px;background:radial-gradient(ellipse at 50% 45%,#6b5048 0%,#3a302d 55%,#2a2524 100%)}
.topbar{left:0;top:0;width:722px;height:43px;background:rgba(30,30,30,.55)}
.brand{left:72px;top:11px;color:var(--white);font-size:22px;font-weight:400;letter-spacing:1px}
.nav{right:72px;top:14px;display:flex;gap:18px;font-size:15px;color:var(--white);text-transform:uppercase}
.nav .active{color:var(--pink)}
.hero-title{left:0;width:722px;text-align:center;color:var(--white);text-transform:uppercase;font-weight:400}
.t1{top:86px;font-size:94px;line-height:1;letter-spacing:1px}
.t2{top:174px;font-size:40px;line-height:1}
.t3{top:220px;font-size:33px;line-height:1}
.hero-btn{left:278px;top:281px;width:175px;height:45px;border:1px solid var(--white);border-radius:3px;color:var(--white);font-size:21px;text-align:center;line-height:43px;text-transform:uppercase}
.arrow{width:18px;height:18px;border-radius:50%;background:#111;top:192px}
.side-tab{left:690px;top:75px;width:32px;height:105px;background:var(--pink);border-radius:6px 0 0 6px;color:var(--white);font-size:9px;font-weight:700;display:flex;flex-direction:column;align-items:center;justify-content:space-around;padding:8px 0}

.promo{left:0;top:365px;width:722px;height:117px;background:linear-gradient(180deg,#f7f7f7,#e4e4e4)}
.promo-photo{left:72px;top:372px;width:128px;height:110px;background:linear-gradient(180deg,#8a5a3e,#2c2020)}
.promo-title{left:200px;width:305px;top:378px;text-align:center;color:var(--green);font-size:19px;line-height:19px;text-transform:uppercase}
.promo-sub{left:200px;width:305px;top:416px;text-align:center;color:var(--pink);font-size:11.5px;font-weight:700;text-transform:uppercase}
.promo-body{left:200px;width:305px;top:439px;text-align:center;font-size:8px;font-weight:700;line-height:18px;color:#333}
.book{background:linear-gradient(160deg,#e9f3d2,#7fb43f 60%,#3f7a28)}

.band-pink{left:0;width:722px;background:linear-gradient(180deg,var(--pink) 0%,var(--pink-deep) 100%)}
.section-title{font-size:20px;font-weight:400;color:var(--white)}
.media-text{left:72px;top:542px;width:390px;font-size:8.3px;line-height:18px;color:var(--white)}
.btn-dark{left:72px;top:612px;width:75px;height:33px;background:#111;border-radius:5px;color:var(--white);font-size:13px;text-align:center;line-height:33px;text-transform:uppercase}
.video{left:491px;top:523px;width:158px;height:111px;border:2px solid var(--white);background:linear-gradient(180deg,#8b8f8c,#404244)}
.pager{color:var(--white);font-size:13px;letter-spacing:4px}

.products-title{left:72px;top:695px;color:var(--pink);font-size:20px;text-transform:uppercase}
.products-pager{left:632px;top:700px;color:#bbb;font-size:13px;letter-spacing:4px}
.cover{top:745px;height:112px;box-shadow:2px 3px 5px rgba(0,0,0,.3)}

.avatar{width:78px;height:78px;border-radius:50%;border:3px solid var(--pink-soft);top:916px}
.avatar-label{top:1010px;width:80px;text-align:center;color:var(--white);font-size:8.5px;font-weight:700;text-transform:uppercase}
.story{left:346px;top:904px;width:303px;height:111px;background:var(--white);border-radius:6px}
.story-head{left:358px;top:912px;width:285px;color:var(--pink);font-size:13.5px;line-height:18px}
.story-body{left:358px;top:955px;width:285px;font-size:7.6px;line-height:18px;color:#222}
.read-more{color:var(--pink);font-size:7px;margin-left:28px}

.seen-title{left:72px;top:1060px;color:var(--pink);font-size:19px}
.seen-row{left:72px;top:1094px;width:570px;display:flex;justify-content:space-between;align-items:center}
.seen-name{font-family:'Yanone Kaffeesatz',sans-serif;font-size:19px;font-weight:600;color:#333}
.next-circle{left:691px;top:1086px;width:21px;height:21px;border-radius:50%;border:2px solid #111}

.footer{left:0;top:1141px;width:722px;height:59px;background:var(--dark)}
.foot-links{left:0;width:722px;top:1157px;text-align:center;color:var(--white);font-size:11px}
.foot-copy{left:0;width:722px;top:1173px;text-align:center;color:var(--white);font-size:10.5px}
.foot-social{left:596px;top:1160px;display:flex;gap:10px;color:var(--pink);font-size:10px;font-weight:700}
</style>
</head>
<body>

<div class="abs hero-photo" role="img" aria-label="Group photo of the team posing in a studio"></div>
<div class="abs topbar"></div>
<div class="abs brand head">KM Valero</div>
<nav class="abs nav head">
  <span class="active">Home</span><span>Products</span><span>About</span><span>Blog</span><span>Forum</span><span>Media Room</span><span>Success Stories</span>
</nav>
<div class="abs hero-title head t1">Discover Serets</div>
<div class="abs hero-title head t2">To A</div>
<div class="abs hero-title head t3">Slimmer Sexier &amp; Healthier You!</div>
<div class="abs hero-btn head">View Our Prodcuts</div>
<svg class="abs arrow" style="left:9px" viewBox="0 0 18 18"><path d="M10.5 5 6.5 9l4 4" stroke="#fff" stroke-width="1.8" fill="none"/></svg>
<svg class="abs arrow" style="left:662px" viewBox="0 0 18 18"><path d="M7.5 5l4 4-4 4" stroke="#fff" stroke-width="1.8" fill="none"/></svg>
<div class="abs side-tab"><span>Post</span><span>Chat</span><span>Clip</span></div>

<div class="abs promo"></div>
<div class="abs promo-photo" role="img" aria-label="Portrait of KM Valero smiling"></div>
<div class="abs promo-title head">The 10-Day Green Blend Reset: Lose up to 15 pounds in 10 days!</div>
<div class="abs promo-sub">What is the 10-Day Green Blend Reset?</div>
<div class="abs promo-body">The 10-Day Green Blend Reset will jump-start your weight loss, increase your energy level, clear your mind, and improve your overall health.</div>
<div class="abs book" style="left:527px;top:377px;width:53px;height:90px" role="img" aria-label="Green Blend Reset book cover"></div>

<div class="abs band-pink" style="top:482px;height:191px"></div>
<div class="abs section-title head" style="left:72px;top:500px">Media Room</div>
<div class="abs pager" style="left:635px;top:497px">‹ ›</div>
<div class="abs media-text">KM is a fabulous guest on radio and TV, and in magazines and newspapers. KM's expertise is in high demand, with appearances on The Sam Harmon Morning Show, The Marla Wade Show, The Jordan Reyes Show, and The Michael Banks Show.</div>
<div class="abs btn-dark head">View Details</div>
<div class="abs video" role="img" aria-label="Video still of KM Valero speaking in a living room"></div>

<div class="abs products-title head">Our Products</div>
<div class="abs products-pager">‹ ›</div>
<div class="abs cover book" style="left:68px;width:62px" role="img" aria-label="Green Blend Reset book cover"></div>
<div class="abs cover" style="left:182px;width:84px;background:linear-gradient(135deg,#f4f0f2,#e46aa8)" role="img" aria-label="Weight loss book cover with author portrait"></div>
<div class="abs cover" style="left:324px;width:64px;background:linear-gradient(135deg,#f3f3f3,#d8a0a0)" role="img" aria-label="Belly fat book cover"></div>
<div class="abs cover" style="left:432px;width:90px;background:linear-gradient(135deg,#f8eaf2,#b9729a)" role="img" aria-label="Look younger DVD set"></div>
<div class="abs cover" style="left:560px;width:88px;background:linear-gradient(135deg,#5aa6a2,#1d5a5a)" role="img" aria-label="Career book cover with money"></div>

<div class="abs band-pink" style="top:865px;height:178px"></div>
<div class="abs section-title head" style="left:72px;top:877px">Success Stories</div>
<div class="abs pager" style="left:632px;top:878px">‹ ›</div>
<div class="abs avatar" style="left:95px;background:linear-gradient(180deg,#a67866,#3a2c2c)" role="img" aria-label="Before photo of Nora Allen"></div>
<div class="abs avatar" style="left:210px;background:linear-gradient(180deg,#d8d0c6,#4a4a58)" role="img" aria-label="After photo of Nora Allen"></div>
<div class="abs avatar-label" style="left:94px">Before</div>
<div class="abs avatar-label" style="left:209px">After</div>
<svg class="abs" style="left:334px;top:916px" width="13" height="18" viewBox="0 0 13 18"><path d="M13 0 0 9l13 9z" fill="#fff"/></svg>
<div class="abs story"></div>
<div class="abs story-head head">"I lost 57 Pounds and No Longer Need Medication for my Diabetes and Cholesterol!" Nora Allen</div>
<div class="abs story-body">I just want to thank you for your book and the KMV system! Prior to the KMV system, I weighed 212 pounds, wore a size 18, was on 5 different medications for high blood pressure, diabetes and high cholesterol.<span class="read-more">READ MORE</span></div>

<div class="abs seen-title head">As Seen On...</div>
<div class="abs seen-row">
  <span class="seen-name">Lumenline</span><span class="seen-name">Brightwave</span><span class="seen-name">Starcast Audio</span><span class="seen-name">Kestrelview</span><span class="seen-name">Gleamora</span><span class="seen-name">Oakfield</span>
</div>
<svg class="abs next-circle" viewBox="0 0 21 21"><circle cx="10.5" cy="10.5" r="7.5" fill="#111"/><path d="M9 7l3.5 3.5L9 14" stroke="#fff" stroke-width="1.6" fill="none"/></svg>

<div class="abs footer"></div>
<div class="abs foot-links head">Privacy Policy &nbsp;|&nbsp; Terms of Use &nbsp;|&nbsp; Disclaimer</div>
<div class="abs foot-copy head">Copyright © 2014companyname.com</div>
<div class="abs foot-social"><span>Post</span><span>Chat</span><span>Clip</span></div>

</body>
</html>
```